Create a premium soap bar box bar design for an all-natural, men's skincare brand.

We are launching a men’s premium, natural soap bar and skincare business. To start, we will be launching cold-press, all-natural soap bars with a few additional products such as lotions. We plan to expand our line into additional skincare products such as face exfoliants, moisturizers and cleansers that target basic needs such as anti-aging, clarifying and hydrating.

Our target audience is men ages 25-50, with a secondary audience of male teens. Our target audience are mid to high income, professionals that live in more urban areas, but enjoy being active outdoors after work and on the weekends. Our target audience are hard workers, humble and want to enjoy all that life has to offer – whether that’s on top of a mountain or an ocean wave. They hike, bike, skateboard, surf or any other sport that gets them outside. They are husbands, brothers and fathers – there for their family and friends.

Our brand is sophisticated, adventurous and has a sense of humor. Many of our competitors either focus on the rugged outdoors or are more pretentious. We are in-between. We are free spirited and love the fresh air. Our products are trustworthy with no toxic chemicals or harsh ingredients. We are all-natural and provide high-quality, premium products that our audience expects and deserves.

Target Market(s)

Men, ages 25-54 who are high-earning professionals, yet enjoy getting outdoors and being active on the weekends - hiking, biking, surfing, skateboarding and more.

Industry/Entity Type

Men's skincare

Font styles to use
Sans Serif

Requirements
Must have
• See attachments
Nice to have
• We would prefer to a have a premium, slightly more modern looking design that will appeal to our target audience and slightly higher price point.
Should not have
• Please do not include an icon for the fragrance, i.e. cinnamon sticks. However, we do need some differentiation for the fragrance, i.e. color, etc. as it will be on the shelf with other fragrances.

```html
<!DOCTYPE html>
<html lang="en">
<head>
<meta charset="utf-8">
<title>Ridge Hale – Men's Natural Soap Range</title>
<link rel="stylesheet" href="https://fonts.googleapis.com/css2?family=Montserrat:wght@300;400;600;700&display=swap">
<style>
  :root {
    --page: #ffffff;
    --band: #262a33;
    --ink: #ffffff;
    --accent: #c85a45;
    --cream: #e8ddcf;
    --cream-strap: #b8a081;
    --terracotta: #c9725a;
    --terracotta-strap: #c75a40;
    --sand: #b59b7b;
    --sand-strap: #a88b69;
  }
  * { box-sizing: border-box; margin: 0; padding: 0; }
  html, body {
    width: 1200px; height: 1000px; overflow: hidden;
    background: var(--page);
    font-family: "Montserrat", sans-serif;
  }
  .range { position: relative; width: 1200px; height: 1000px; }
  .soap-box {
    position: absolute; top: 313px;
    width: 326px; height: 377px;
    background: var(--box-bg);
  }
  .soap-box--ember { left: 62px;  --box-bg: var(--cream);      --strap: var(--cream-strap); }
  .soap-box--bold  { left: 434px; --box-bg: var(--terracotta); --strap: var(--terracotta-strap); }
  .soap-box--scrub { left: 814px; --box-bg: var(--sand);       --strap: var(--sand-strap); }

  .label-band {
    position: absolute; top: 0; left: 78px;
    width: 169px; height: 100%;
    background: var(--band);
    border-left: 11px solid var(--strap);
    border-right: 11px solid var(--strap);
    color: var(--ink);
    text-align: center;
  }
  .brand-dot {
    width: 40px; height: 40px; border-radius: 50%;
    background: var(--accent);
    border: 2px solid var(--ink);
    margin: 98px auto 0;
  }
  .brand-name {
    margin-top: 6px;
    font-size: 15px; font-weight: 400; letter-spacing: 1.5px;
    line-height: 18px;
  }
  .brand-tagline {
    margin-top: 0;
    font-size: 5px; font-weight: 600; letter-spacing: 2.2px;
    line-height: 7px;
  }
  .product-name {
    margin-top: 17px;
    font-size: 16px; font-weight: 600; line-height: 19px;
    text-transform: uppercase;
  }
  .product-type {
    margin-top: 4px;
    font-size: 11px; font-weight: 600;
  }
  .net-weight {
    position: absolute; left: 0; right: 0; bottom: 16px;
    font-size: 10px; font-weight: 600;
  }
</style>
</head>
<body>
<main class="range">
  <article class="soap-box soap-box--ember">
    <div class="label-band">
      <div class="brand-dot"></div>
      <p class="brand-name">RIDGE HALE</p>
      <p class="brand-tagline">TRUE SKIN GOODS</p>
      <h2 class="product-name">Cedar<br>Ember</h2>
      <p class="product-type">Men’s Natural Soap</p>
      <p class="net-weight">5 Oz. Bar</p>
    </div>
  </article>

  <article class="soap-box soap-box--bold">
    <div class="label-band">
      <div class="brand-dot"></div>
      <p class="brand-name">RIDGE HALE</p>
      <p class="brand-tagline">TRUE SKIN GOODS</p>
      <h2 class="product-name">Warm &amp;<br>Bold</h2>
      <p class="product-type">Men’s Natural Soap</p>
      <p class="net-weight">5 Oz. Bar</p>
    </div>
  </article>

  <article class="soap-box soap-box--scrub">
    <div class="label-band">
      <div class="brand-dot"></div>
      <p class="brand-name">RIDGE HALE</p>
      <p class="brand-tagline">TRUE SKIN GOODS</p>
      <h2 class="product-name">Trail<br>Scrub</h2>
      <p class="product-type">Men’s Natural Soap</p>
      <p class="net-weight">5 Oz. Bar</p>
    </div>
  </article>
</main>
</body>
</html>
```